Brookvale Building Company - advertisement poster

I am looking to print some canvas signs to advertise my general contracting company, Brookvale Building Company. The sign will measure 6' long x 3' high so the size should match that ratio. I already have a logo icon, which is the Letter 'B' and some trees that I would like to incorporate, see attached. I would also like the to have the following information listed:
1) phone number: 831-555-0172
2) email: brookvalebuildingcompany@mailnest.example
3) website: brookvalebuildingcompany.example
4) Lic#4826130
5) I want to use this text: "BUILD WITH THE B-CREW!"

The ad should be relatively simple and clean. Black and Green are my company colors. I am open to creative ideas!

Target Market(s)

People looking to renovate their homes

Industry/Entity Type

Construction

Colors
59FF00
82FF00
B8FF75
E3FFCB
F4FFEA

Requirements
Must have
• Must have my company logo
Should not have
• No photos or complex graphics

```html
<!DOCTYPE html>
<html lang="en">
<head>
<meta charset="utf-8">
<title>Brookvale Building Company – Sign</title>
<link rel="stylesheet" href="https://fonts.googleapis.com/css2?family=Montserrat:wght@400;500;600;700;800&display=swap">
<style>
  :root {
    --brand-green: #72b548;
    --ink: #000000;
    --paper: #ffffff;
  }
  * { box-sizing: border-box; margin: 0; padding: 0; }
  html, body {
    width: 1200px; height: 699px; overflow: hidden;
    background: var(--paper);
    font-family: "Montserrat", sans-serif;
  }
  .canvas { position: relative; width: 1200px; height: 699px; }

  .sign {
    position: absolute; left: 93px; top: 92px;
    width: 1014px; height: 515px;
    background: var(--brand-green);
    box-shadow: 0 0 14px rgba(0,0,0,0.12);
  }
  .hero-panel {
    position: absolute; left: 22px; top: 22px;
    width: 970px; height: 362px;
    background: var(--ink);
    border-radius: 46px;
  }

  /* company name block */
  .company-name {
    position: absolute; left: 40px; top: 118px; width: 360px;
    text-align: center; color: var(--paper);
    font-weight: 700; line-height: 1;
  }
  .company-name .line-main { display: block; font-size: 44px; letter-spacing: 1px; }
  .company-name .line-sub { display: block; font-size: 16.5px; letter-spacing: 5px; margin-top: 10px; }

  .license-badge {
    position: absolute; left: 145px; top: 241px;
    width: 155px; height: 38px;
    border: 3px solid var(--brand-green); border-radius: 16px;
    color: var(--paper); font-size: 18px; font-weight: 400;
    display: flex; align-items: center; justify-content: center;
  }

  /* headline */
  .headline-frame { position: absolute; left: 396px; top: 69px; }
  .headline {
    position: absolute; left: 428px; top: 84px;
    color: var(--paper); line-height: 1;
  }
  .headline .lead { display: block; font-size: 62px; font-weight: 500; letter-spacing: 0; }
  .headline .crew { display: block; font-size: 104px; font-weight: 800; margin-top: 6px; letter-spacing: -1px; }
  .headline .crew-letter { color: var(--brand-green); }

  /* contact row */
  .contact-row { position: absolute; left: 0; top: 0; width: 100%; height: 100%; }
  .phone-icon { position: absolute; left: 21px; top: 410px; }
  .phone-number {
    position: absolute; left: 111px; top: 426px;
    font-size: 40px; font-weight: 700; color: var(--ink); letter-spacing: -1px; line-height: 1;
  }
  .contact-icon { position: absolute; top: 431px; }
  .contact-link {
    position: absolute; top: 440px;
    font-size: 10px; font-weight: 600; color: var(--ink); line-height: 1;
    padding-bottom: 3px; border-bottom: 1.5px solid var(--ink);
    text-decoration: none;
  }
  .contact-link.web { left: 427px; }
  .contact-link.mail { left: 715px; font-size: 9px; top: 441px; }
</style>
</head>
<body>
<div class="canvas">
  <section class="sign">
    <div class="hero-panel"></div>

    <div class="company-name">
      <span class="line-main">BROOKVALE</span>
      <span class="line-sub">BUILDING COMPANY</span>
    </div>
    <div class="license-badge">LIC#4826130</div>

    <svg class="headline-frame" width="600" height="206" viewBox="0 0 600 206" aria-hidden="true">
      <polyline points="595,2 2,2 2,202 476,202" fill="none" stroke="#ffffff" stroke-width="4"/>
    </svg>
    <h1 class="headline">
      <span class="lead">BUILD WITH THE</span>
      <span class="crew"><span class="crew-letter">B</span> CREW!</span>
    </h1>

    <div class="contact-row">
      <svg class="phone-icon" width="74" height="74" viewBox="0 0 74 74" aria-hidden="true">
        <circle cx="37" cy="37" r="34" fill="none" stroke="#000" stroke-width="4"/>
        <path d="M20 22c2-3 5-4 7-2l4 6c1 2 0 4-2 5l-2 1c2 5 6 9 11 11l1-2c1-2 3-3 5-2l6 4c2 2 1 5-2 7-4 3-10 2-17-4-8-6-13-14-13-19 0-2 1-4 2-5z" fill="#000"/>
        <path d="M40 22a12 12 0 0 1 12 12M42 16a18 18 0 0 1 16 16M38 28a6 6 0 0 1 6 6" fill="none" stroke="#000" stroke-width="2.5" stroke-linecap="round"/>
      </svg>
      <div class="phone-number">831-555-0172</div>

      <svg class="contact-icon" style="left:382px" width="32" height="32" viewBox="0 0 32 32" aria-hidden="true">
        <circle cx="16" cy="16" r="16" fill="#000"/>
        <circle cx="15" cy="16" r="8" fill="none" stroke="#72b548" stroke-width="1"/>
        <ellipse cx="15" cy="16" rx="3.5" ry="8" fill="none" stroke="#72b548" stroke-width="1"/>
        <path d="M7 16h16M8.5 12h13M8.5 20h13" stroke="#72b548" stroke-width="1"/>
      </svg>
      <a class="contact-link web">BROOKVALEBUILDINGCOMPANY.EXAMPLE</a>

      <svg class="contact-icon" style="left:672px" width="32" height="32" viewBox="0 0 32 32" aria-hidden="true">
        <circle cx="16" cy="16" r="16" fill="#000"/>
        <rect x="8.5" y="11" width="15" height="10" fill="none" stroke="#72b548" stroke-width="1.2"/>
        <path d="M8.5 11l7.5 6 7.5-6M8.5 21l5.5-5M23.5 21l-5.5-5" fill="none" stroke="#72b548" stroke-width="1.2"/>
      </svg>
      <a class="contact-link mail">BROOKVALEBUILDINGCOMPANY@MAILNEST.EXAMPLE</a>
    </div>
  </section>
</div>
</body>
</html>
```